Global (re)insurance broker needs a business card design

We need a classic business card for our company that is headquartered in SG, with offices in Malaysia and Dubai. We specialise in insurance and reinsurance broking and consultancy for our global clients.

```html
<!DOCTYPE html>
<html lang="en">
<head>
<meta charset="utf-8">
<title>Meridale Business Card</title>
<link href="https://fonts.googleapis.com/css2?family=Open+Sans:wght@400;600;800&display=swap" rel="stylesheet">
<style>
  :root{
    --stage:#2a2a2d;
    --card:#161616;
    --brand-blue:#2a4a9e;
    --mint:#c6e0bd;
    --ink:#f2f2f2;
    --ghost:#222224;
  }
  *{box-sizing:border-box;margin:0;padding:0}
  html,body{width:1200px;height:947px;overflow:hidden}
  body{background:var(--stage);font-family:"Open Sans",sans-serif;position:relative}
  .card{position:absolute;width:620px;height:354px;background:var(--card);
    border:3px solid var(--brand-blue);border-radius:28px;overflow:hidden}
  .card-back{left:80px;top:90px}
  .card-front{left:500px;top:500px}
  .back-wordmark{position:absolute;left:0;right:0;top:50%;transform:translateY(-50%);
    text-align:center;font-weight:800;font-size:104px;letter-spacing:2px;color:var(--ghost)}
  .front-wordmark{position:absolute;left:34px;top:150px;width:240px;white-space:nowrap;
    font-weight:800;font-size:42px;line-height:1;color:var(--mint)}
  .divider{position:absolute;left:296px;top:38px;width:2px;height:220px;background:var(--mint)}
  .details{position:absolute;left:318px;top:34px;color:var(--ink);font-size:13px;line-height:1.45}
  .person-name{font-weight:800;font-size:21px;line-height:1.1}
  .person-name .first{color:var(--brand-blue)}
  .person-name .last{color:var(--mint)}
  .person-role{font-size:14px;margin-bottom:12px}
  .contact-list{list-style:none;margin-bottom:12px}
  .contact-list li{display:flex;align-items:center;gap:7px}
  .contact-list svg{width:12px;height:12px;flex:none}
  .wave{position:absolute;left:0;top:0;width:100%;height:100%}
</style>
</head>
<body>
  <div class="card card-back">
    <div class="back-wordmark">MERIDALE</div>
  </div>

  <div class="card card-front">
    <svg class="wave" viewBox="0 0 614 348" preserveAspectRatio="none" aria-hidden="true">
      <path d="M614 118 C520 200 330 250 270 348 L614 348 Z" fill="var(--brand-blue)"/>
      <path d="M614 96 C520 190 330 236 250 348 L262 348 C340 246 520 204 614 112 Z" fill="var(--mint)"/>
      <path d="M614 114 C520 198 330 246 262 348" fill="none" stroke="var(--card)" stroke-width="4"/>
    </svg>

    <div class="front-wordmark">MERIDALE</div>
    <div class="divider"></div>

    <div class="details">
      <p class="person-name"><span class="first">Hana</span> <span class="last">Lim</span></p>
      <p class="person-role">Chief Operating Officer</p>
      <ul class="contact-list">
        <li><svg viewBox="0 0 24 24"><path fill="var(--ink)" d="M6.6 10.8a15 15 0 006.6 6.6l2.2-2.2a1 1 0 011-.25 11.4 11.4 0 003.6.57 1 1 0 011 1V20a1 1 0 01-1 1A17 17 0 013 4a1 1 0 011-1h3.5a1 1 0 011 1c0 1.25.2 2.45.57 3.57a1 1 0 01-.25 1z"/></svg>+65 9000 1234</li>
        <li><svg viewBox="0 0 24 24"><path fill="var(--ink)" d="M2 5h20v14H2z M2 5l10 8 10-8" stroke="var(--card)" stroke-width="1.5"/></svg>hana@meridale.com</li>
        <li><svg viewBox="0 0 24 24"><circle cx="12" cy="12" r="10" fill="var(--ink)"/><path d="M2 12h20M12 2c3 3 3 17 0 20M12 2c-3 3-3 17 0 20" stroke="var(--card)" stroke-width="1.5" fill="none"/></svg>www.meridale.com</li>
      </ul>
      <p class="address">28 Harbour Lane,<br>Marina Tower #08-04,<br>Singapore 049000</p>
    </div>
  </div>
</body>
</html>
```